An insurance broker wants to represent the company's vision visually and textually.

My company, with a total of 10 employees, developed a vision this year. Now, we want to display this vision in the form of a two-meter-high visual that will be mounted on the wall. This ensures that the vision is always visible to our employees, as well as to our clients and partners when they visit our office.

Here's my idea: the vision will be accompanied by a fitting image, with the text of the vision itself elegantly written in a beautiful font. Our vision reads: "Every company always has a perfectly tailored future solution for greater financial security, freedom, and joy."

A bit about my company: we are an insurance broker, and our services are primarily designed for corporate clients.

```html
<!DOCTYPE html>
<html lang="en">
<head>
<meta charset="utf-8">
<title>Our Vision</title>
<link rel="stylesheet" href="https://fonts.googleapis.com/css2?family=Playfair+Display:wght@900&family=Yellowtail&family=League+Spartan:wght@700&display=swap">
<style>
  :root {
    --navy: #2a2552;
    --navy-deep: #221e47;
    --teal: #10ae9f;
    --amber: #e8a833;
    --gold-script: #f4d06f;
    --white: #ffffff;
  }
  html, body {
    margin: 0;
    padding: 0;
    overflow: hidden;
  }
  .vision-poster {
    position: relative;
    width: 1200px;
    height: 1200px;
    overflow: hidden;
    background: radial-gradient(ellipse at 50% 45%, var(--navy) 0%, var(--navy) 55%, var(--navy-deep) 100%);
  }
  .hero-art {
    position: absolute;
    left: 328px;
    top: 56px;
    width: 547px;
    height: 326px;
    border-radius: 8px;
    background: linear-gradient(135deg, var(--teal) 0%, var(--amber) 50%, var(--teal) 100%);
    opacity: 0.9;
  }
  .frame-corners {
    position: absolute;
    left: 0;
    top: 0;
  }
  .vision-line {
    position: absolute;
    left: 0;
    width: 1200px;
    margin: 0;
    text-align: center;
    line-height: 1;
    white-space: nowrap;
  }
  .serif-caps {
    font-family: "Playfair Display", serif;
    font-weight: 900;
    text-transform: uppercase;
  }
  .script {
    font-family: "Yellowtail", cursive;
    color: var(--gold-script);
    font-size: 62px;
  }
  .sans-caps {
    font-family: "League Spartan", sans-serif;
    font-weight: 700;
    text-transform: uppercase;
    color: var(--white);
    font-size: 80px;
    letter-spacing: 1px;
  }
  .line-company { top: 425px; color: var(--teal); font-size: 88px; letter-spacing: 5px; }
  .line-always { top: 528px; }
  .line-tailored { top: 605px; color: var(--white); font-size: 78px; letter-spacing: 4px; }
  .line-solution { top: 695px; color: var(--white); font-size: 66px; letter-spacing: 3px; }
  .line-greater { top: 766px; }
  .line-financial { top: 870px; }
  .line-security { top: 966px; }
  .line-joy { top: 1060px; }
</style>
</head>
<body>
<main class="vision-poster">
  <div class="hero-art" role="img" aria-label="Illustration of interlocking puzzle pieces stacked into a pyramid in teal, amber and white"></div>

  <svg class="frame-corners" width="1200" height="1200" viewBox="0 0 1200 1200" aria-hidden="true">
    <g fill="none" stroke="var(--white)" stroke-width="8">
      <polyline points="116,463 116,392 189,392"/>
      <polyline points="1011,392 1084,392 1084,463"/>
      <polyline points="116,1071 116,1142 189,1142"/>
      <polyline points="1011,1142 1084,1142 1084,1071"/>
    </g>
  </svg>

  <h1 class="vision-line serif-caps line-company">Every Company</h1>
  <p class="vision-line script line-always">always has a</p>
  <p class="vision-line serif-caps line-tailored">Perfectly Tailored</p>
  <p class="vision-line serif-caps line-solution">Future Solution</p>
  <p class="vision-line script line-greater">for greater</p>
  <p class="vision-line sans-caps line-financial">Financial</p>
  <p class="vision-line sans-caps line-security">Security, Freedom</p>
  <p class="vision-line sans-caps line-joy">and Joy.</p>
</main>
</body>
</html>
```